I want a website to be designed for our new company, it's an import and export company for variety of things.

please see the attached Logo for our company and the Images for our different sections for our busienss

Target Market(s)

multiple

Coding

Coded - Design and coding required

Number of Pages Required

5+ page

Font styles to use
Sans Serif

Colors

Designer to choose colors to be used in the design.

Requirements
Must have
• KVR GLOBALINKS
• KVR globalinks Trading & Contracting provides various services. The Company offers infrastructure construction, oil, enegy and gas services, agricultural projects, real estate development, travel and tourism, and food processing and trading.
• Civil contracting for infrastructure, residential and heavy projects. Through its main subsidiaries; distribution of general food products, construction chemicals including corrosion inhibitors and electrical machinery; provides catering and travel agency services; ownership and operation of a school; offers human sources services including manpower supply.
• Drilling and Gold Mines Used Machinery, All Kinds of Construction Machinery, Drilling Machines are manufactured and sold.
Nice to have
• good designa and beautiful colours, it has too look professional

```html
<!DOCTYPE html>
<html lang="en">
<head>
<meta charset="utf-8">
<title>KVR Globalinks – Import &amp; Export</title>
<link href="https://fonts.googleapis.com/css2?family=Montserrat:wght@400;500;600;700&display=swap" rel="stylesheet">
<style>
:root{
  --gold:#f4c400;
  --gold-text:#e9b800;
  --ink:#0e0e0e;
  --bar:#191919;
  --header:#121212;
  --panel:#1d1d1d;
  --panel-2:#262626;
  --card:#2b2b2b;
  --grey:#9b9b9b;
  --line:#5a5a5a;
  --white:#ffffff;
  --muted:#c9c9c9;
}
*{margin:0;padding:0;box-sizing:border-box}
html,body{width:1200px;height:4367px;overflow:hidden}
body{position:relative;background:var(--ink);font-family:'Montserrat',sans-serif;color:var(--white)}
.section{position:absolute;left:0;width:1200px;overflow:hidden}
.abs{position:absolute}
.center{left:0;width:1200px;text-align:center}

/* top bar */
.topbar{top:0;height:42px;background:var(--bar);font-size:11px;color:var(--muted)}
.topbar .item{top:14px;display:flex;align-items:center;gap:7px}
.topbar svg{display:block}
.flag{width:30px;height:16px;background:#c7c7c7;border-radius:1px}

/* header */
.header{top:42px;height:136px;background:var(--header)}
.brand{left:118px;top:44px;display:flex;align-items:center;gap:8px;font-size:14px;font-weight:600;letter-spacing:1px;color:var(--white)}
.brand .dot{width:14px;height:14px;border-radius:50%;background:var(--gold)}
.social{top:22px;left:330px;display:flex;gap:12px}
.social span{width:28px;height:28px;border-radius:50%;background:#e5e5e5}
.nav{top:73px;left:338px;display:flex;gap:0;font-size:11px;font-weight:500}
.nav a{color:var(--white);text-decoration:none;margin-right:23px}
.nav a.active{color:var(--gold);border-bottom:2px solid var(--gold);padding-bottom:6px}
.divider{left:810px;top:0;width:1px;height:136px;background:#333}
.search-label{left:833px;top:28px;font-size:11px;font-weight:500}
.search{left:832px;top:55px;width:255px;height:38px;border:1px solid #bbb;border-radius:20px;font-size:11px;color:#aaa;padding:12px 16px}
.search i{position:absolute;right:6px;top:6px;width:24px;height:24px;border-radius:50%;background:#e5e5e5}

/* hero */
.hero{top:178px;height:514px;background:linear-gradient(180deg,#3c4352 0%,#6f5e4a 30%,#a8642c 48%,#3b3a3d 70%,#1d1d22 100%)}
.hero .kicker{top:155px;font-size:12px;color:var(--gold);letter-spacing:.3px}
.hero h1{top:180px;font-size:46px;font-weight:600;letter-spacing:.5px}
.btn-outline{left:532px;top:267px;width:136px;height:38px;border:1px solid #ddd;border-radius:20px;font-size:11px;font-weight:600;text-align:center;line-height:36px}
.dots{top:440px;display:flex;justify-content:center;gap:5px}
.dots span{width:10px;height:10px;border-radius:50%;background:#ddd}

/* headings */
.eyebrow{font-size:20px;color:var(--gold-text);font-weight:400}
.title{font-size:38px;font-weight:600;letter-spacing:.5px}
.ornament{left:513px;width:175px;height:28px;border-radius:14px;background:linear-gradient(90deg,#555,#d8d8d8,#555)}

/* welcome */
.welcome{top:692px;height:618px;background:linear-gradient(180deg,#1b1b1b,#262422 60%,#1e1e1e)}
.welcome p.lead{top:225px;left:170px;width:860px;font-size:13px;line-height:26px;color:#d5d5d5;text-align:center}
.diagram{left:0;top:0}
.label{font-size:13px;font-weight:500;line-height:16px}
.label.right{text-align:right}

/* services */
.services{top:1310px;height:792px;background:linear-gradient(180deg,#2a2a2a,#1f1f1f)}
.tabs{top:245px;left:387px;display:flex;gap:10px}
.tabs span{width:135px;height:52px;background:var(--grey);font-size:12px;text-align:center;line-height:52px}
.tabs span.on{background:var(--gold);color:#222}
.tabline{top:298px;left:112px;width:976px;height:4px;background:var(--line)}
.card{top:348px;width:312px;height:360px;background:var(--card)}
.card .img{height:218px}
.card h3{position:absolute;left:23px;top:238px;font-size:16px;font-weight:600;line-height:25px;text-transform:uppercase}
.card p{position:absolute;left:23px;top:300px;width:270px;font-size:12px;line-height:23px;color:#c7c7c7}
.card.feature{background:var(--gold)}
.card.feature h3{color:#222}
.card.feature p{color:#6b5600}

/* news */
.news{top:2102px;height:746px;background:linear-gradient(180deg,#181818,#222)}
.ncard{background:#000;border:1px solid #2e2e2e}
.meta{font-size:9px;font-weight:600;color:var(--gold);display:flex;gap:22px}
.ntitle{font-size:11px;font-weight:600;line-height:21px}
.ntext{font-size:9.5px;line-height:17px;color:#8d8d8d}
.more{font-size:10px;font-weight:700;color:var(--gold);text-decoration:underline}

/* gallery */
.gallery{top:2848px;height:881px;background:linear-gradient(180deg,#222,#1a1a1a)}
.gi{position:absolute;width:315px}
.gi span{position:absolute;left:20px;bottom:16px;font-size:10.5px;font-weight:600}

/* partners */
.partners{top:3729px;height:203px;background:#151515}
.arrow{top:94px}
.pshape{top:80px;width:56px;height:56px;background:#cfcfcf}

/* footer */
.footer{top:3932px;height:435px;background:var(--ink)}
.fhead{font-size:20px;font-weight:600;top:50px}
.qlinks{left:112px;top:117px;list-style:none;font-size:11.5px;font-weight:600}
.qlinks li{height:30.6px}
.qlinks li::before{content:"»";margin-right:8px}
.field{height:42px;width:240px;background:#e4e4e4;font-size:11px;color:#888;padding:14px 18px}
.submit{background:var(--gold);color:#111;font-weight:700;text-align:center;padding:14px 0}
.contact{left:874px;font-size:11.5px;font-weight:600;line-height:31px;display:flex;gap:14px}
.contact svg{flex:none;margin-top:9px}
.fline{left:112px;top:355px;width:976px;height:4px;background:#777}
.copy{top:390px;font-size:12px;color:#ddd}
</style>
</head>
<body>

<!-- top bar -->
<div class="section topbar">
  <div class="abs item" style="left:110px">
    <svg width="12" height="9" viewBox="0 0 12 9"><rect width="12" height="9" fill="#f4c400"/><path d="M0 0l6 5 6-5" stroke="#191919" fill="none"/></svg>
    info@kvrglobalinks.com
  </div>
  <div class="abs item" style="left:330px">
    <svg width="11" height="11" viewBox="0 0 24 24"><path fill="#f4c400" d="M6.6 10.8a15 15 0 0 0 6.6 6.6l2.2-2.2c.3-.3.7-.4 1-.2 1.1.4 2.3.6 3.6.6.6 0 1 .4 1 1V20c0 .6-.4 1-1 1C10.6 21 3 13.4 3 4c0-.6.4-1 1-1h3.5c.6 0 1 .4 1 1 0 1.3.2 2.5.6 3.6.1.3 0 .7-.2 1z"/></svg>
    +1 555 010 2030
  </div>
  <div class="abs item" style="left:820px">
    <svg width="10" height="11" viewBox="0 0 10 11"><circle cx="5" cy="3" r="3" fill="#f4c400"/><path d="M0 11a5 5 0 0 1 10 0z" fill="#f4c400"/></svg>
    Login
  </div>
  <div class="abs item" style="left:895px">
    <svg width="9" height="11" viewBox="0 0 9 11"><rect y="5" width="9" height="6" fill="#f4c400"/><path d="M2 5V3a2.5 2.5 0 0 1 5 0v2" stroke="#f4c400" fill="none"/></svg>
    Registration
  </div>
  <div class="abs item" style="left:1015px;top:11px">ENG ▾ <span class="flag"></span></div>
</div>

<!-- header -->
<header class="section header">
  <div class="abs brand"><span class="dot"></span>KVR GLOBALINKS</div>
  <div class="abs social"><span></span><span></span><span></span></div>
  <nav class="abs nav">
    <a class="active" href="#">HOME</a><a href="#">ABOUT US</a><a href="#">SERVICES</a><a href="#">SHIPPING</a><a href="#">BLOG</a><a href="#">CONTACT US</a>
  </nav>
  <div class="abs divider"></div>
  <div class="abs search-label">SEARCH FOR :</div>
  <div class="abs search">Search<i></i></div>
</header>

<!-- hero -->
<section class="section hero" role="img" aria-label="Cargo plane on a runway in front of port cranes and container ship at sunset">
  <div class="abs center kicker">WE ARE AN IMPORT AND EXPORT COMPANY FOR A VARIETY OF THINGS</div>
  <h1 class="abs center">KVR GLOBALINKS</h1>
  <div class="abs btn-outline">GET STARTED</div>
  <div class="abs center dots"><span></span><span></span><span></span></div>
</section>

<!-- welcome -->
<section class="section welcome">
  <div class="abs center eyebrow" style="top:90px">WELCOME</div>
  <h2 class="abs center title" style="top:116px">KVR GLOBALINKS</h2>
  <div class="abs ornament" role="img" aria-label="Silver scroll ornament" style="top:174px"></div>
  <p class="abs lead">Lorem ipsum dolor sit amet, consectetur adipiscing elit, sed do eiusmod tempor incididunt ut labore et dolore magna aliqua. Ut enim ad minim veniam, quis nostrud exercitation ullamco laboris nisi ut aliquip ex ea commodo consequat. Duis aute irure dolor in reprehenderit in voluptate velit esse cillum dolore.</p>

  <svg class="abs diagram" width="1200" height="618" viewBox="0 0 1200 618">
    <path d="M278 581 A 325 195 0 0 1 922 581" fill="none" stroke="#bdbdbd" stroke-width="3"/>
    <g fill="#d9d9d9" stroke="#1e1e1e" stroke-width="4">
      <circle cx="600" cy="393" r="37"/><circle cx="458" cy="411" r="37"/><circle cx="735" cy="411" r="37"/>
      <circle cx="330" cy="486" r="37"/><circle cx="865" cy="488" r="37"/>
      <circle cx="278" cy="581" r="37"/><circle cx="915" cy="581" r="37"/>
    </g>
    <g fill="#ffffff">
      <circle cx="600" cy="393" r="14"/><circle cx="458" cy="411" r="14"/><circle cx="735" cy="411" r="14"/>
      <circle cx="330" cy="486" r="14"/><circle cx="865" cy="488" r="14"/>
      <circle cx="278" cy="581" r="14"/><circle cx="915" cy="581" r="14"/>
    </g>
    <circle cx="520" cy="525" r="7" fill="#f4c400"/>
    <text x="532" y="531" fill="#ffffff" font-family="Montserrat, sans-serif" font-size="16" font-weight="600" letter-spacing="1">KVR GLOBALINKS</text>
  </svg>

  <div class="abs center label" style="top:330px">Agricultural projects</div>
  <div class="abs label right" style="left:280px;width:125px;top:388px">Enegy and<br>Gas services</div>
  <div class="abs label" style="left:788px;top:392px">Real estate<br>Development</div>
  <div class="abs label right" style="left:200px;width:78px;top:474px">Oil</div>
  <div class="abs label" style="left:918px;top:474px">Travel and<br>Tourism</div>
  <div class="abs label right" style="left:80px;width:145px;top:560px">Infrastructure<br>Construction</div>
  <div class="abs label" style="left:968px;top:562px">Food processing<br>&amp; Trading</div>
</section>

<!-- services -->
<section class="section services">
  <div class="abs center eyebrow" style="top:92px">KVR GLOBALINKS</div>
  <h2 class="abs center title" style="top:120px">PROVIDES VARIOUS SERVICES</h2>
  <div class="abs ornament" role="img" aria-label="Silver scroll ornament" style="top:178px"></div>
  <div class="abs tabs"><span>All</span><span class="on">Trading</span><span>Contracting</span></div>
  <div class="abs tabline"></div>

  <article class="abs card" style="left:112px">
    <div class="img" role="img" aria-label="Oil refinery under stormy sky" style="background:linear-gradient(180deg,#6d7583,#4a4a4f 55%,#8a4a22)"></div>
    <h3>Oil, enegy and gas<br>services</h3>
    <p>Lorem ipsum dolor sit amet, consectetura dipiscing elit, sed do eiusmod</p>
  </article>
  <article class="abs card feature" style="left:442px">
    <div class="img" role="img" aria-label="Shelves of packaged general food products" style="background:linear-gradient(135deg,#8b2a1e,#c8a24a 45%,#3d5a8a)"></div>
    <h3>Distribution of general<br>food products</h3>
    <p>Lorem ipsum dolor sit amet, consectetura dipiscing elit, sed do eiusmod</p>
  </article>
  <article class="abs card" style="left:773px">
    <div class="img" role="img" aria-label="Farmer checking crops with a digital tablet" style="background:linear-gradient(135deg,#52604a,#8e9a7a 50%,#3f4b3a)"></div>
    <h3>Agricultural<br>projects</h3>
    <p>Lorem ipsum dolor sit amet, consectetura dipiscing elit, sed do eiusmod</p>
  </article>
</section>

<!-- news -->
<section class="section news">
  <div class="abs center eyebrow" style="top:92px">NEWS</div>
  <h2 class="abs center title" style="top:120px">LATEST NEWS &amp; ARTICLES</h2>
  <div class="abs ornament" role="img" aria-label="Silver scroll ornament" style="top:180px"></div>

  <article class="abs ncard" style="left:112px;top:236px;width:480px;height:410px">
    <div class="abs" role="img" aria-label="Handshake over a small model house" style="left:6px;top:6px;width:466px;height:261px;background:linear-gradient(135deg,#ddd,#8a8178 55%,#3a302a)"></div>
    <div class="abs meta" style="left:26px;top:296px"><span>▣ JAN 04,2020</span><span>▢ 4</span></div>
    <div class="abs ntitle" style="left:26px;top:318px">Lorem ipsum dolor sit amet, consectetur adipiscing elit, sed do</div>
    <div class="abs ntext" style="left:26px;top:344px;width:420px">Lorem ipsum dolor sit amet, consectetur adipiscing elit, sed do eiusmod tempor incididunt ut labore et dolore magna aliqua. Ut enim ad minim ve quis nostrud exercitation ullamco laboris nisi ut</div>
  </article>

  <article class="abs ncard" style="left:600px;top:236px;width:488px;height:200px">
    <div class="abs" role="img" aria-label="Engineer working on industrial piping" style="left:5px;top:5px;width:197px;height:190px;background:linear-gradient(135deg,#c4c4c4,#8b7a50 50%,#4c4a45)"></div>
    <div class="abs meta" style="left:225px;top:30px"><span>▣ JAN 04,2020</span><span>▢ 4</span></div>
    <div class="abs ntitle" style="left:225px;top:52px;width:245px">Lorem ipsum dolor sit amet, consectetur adipiscing elit, sed do</div>
    <div class="abs ntext" style="left:225px;top:97px;width:245px">Lorem ipsum dolor sit amet, consectetur adipis cing elit, sed do eiusmod tempor incididunt ut labore et dolore magna aliqua.</div>
    <div class="abs more" style="left:225px;top:160px">Read More »</div>
  </article>

  <article class="abs ncard" style="left:600px;top:448px;width:488px;height:198px">
    <div class="abs" role="img" aria-label="Power drill and tools on a wooden table" style="left:5px;top:5px;width:197px;height:188px;background:linear-gradient(135deg,#3c3630,#7a6a58 50%,#2c2620)"></div>
    <div class="abs meta" style="left:225px;top:30px"><span>▣ JAN 04,2020</span><span>▢ 4</span></div>
    <div class="abs ntitle" style="left:225px;top:52px;width:245px">Lorem ipsum dolor sit amet, consectetur adipiscing elit, sed do</div>
    <div class="abs ntext" style="left:225px;top:97px;width:245px">Lorem ipsum dolor sit amet, consectetur adipis cing elit, sed do eiusmod tempor incididunt ut labore et dolore magna aliqua.</div>
    <div class="abs more" style="left:225px;top:160px">Read More »</div>
  </article>
</section>

<!-- gallery -->
<section class="section gallery">
  <div class="abs center eyebrow" style="top:90px">GALLERY</div>
  <h2 class="abs center title" style="top:118px">GALLERY WITH LIGHTBOX</h2>
  <div class="abs ornament" role="img" aria-label="Silver scroll ornament" style="top:175px"></div>

  <div class="gi" role="img" aria-label="Assorted groceries, wine and vegetables" style="left:112px;top:230px;height:215px;background:linear-gradient(180deg,#eaeaea,#9c6a3a 70%,#5a3a20)"><span>Lorem ipsum dolor sit amet, consectetur</span></div>
  <div class="gi" role="img" aria-label="Fuel nozzle filling a vehicle" style="left:112px;top:452px;height:343px;background:linear-gradient(135deg,#2a3140,#1b2230 55%,#3a2a20)"><span>Lorem ipsum dolor sit amet, consectetur</span></div>
  <div class="gi" role="img" aria-label="Excavator arm against a blue sky" style="left:443px;top:230px;height:349px;background:linear-gradient(180deg,#2c4a78,#5a7aa0 55%,#3a3f48)"><span>Lorem ipsum dolor sit amet, consectetur</span></div>
  <div class="gi" role="img" aria-label="Travellers looking at a map outdoors" style="left:443px;top:587px;height:208px;background:linear-gradient(135deg,#8aa05a,#c2a070 50%,#5a6a3a)"><span>Lorem ipsum dolor sit amet, consectetur</span></div>
  <div class="gi" role="img" aria-label="Family planting seedlings in a garden" style="left:773px;top:230px;height:212px;background:linear-gradient(135deg,#6a4a30,#a08060 50%,#4a5a30)"><span>Lorem ipsum dolor sit amet, consectetur</span></div>
  <div class="gi" role="img" aria-label="Construction crane silhouette at golden sunset" style="left:773px;top:449px;height:346px;background:linear-gradient(180deg,#3a3320,#d6a420 55%,#6a4a10)"><span>Lorem ipsum dolor sit amet, consectetur</span></div>
</section>

<!-- partners -->
<section class="section partners">
  <svg class="abs arrow" style="left:50px" width="14" height="24" viewBox="0 0 14 24"><path d="M12 2L2 12l10 10" stroke="#ddd" stroke-width="2.5" fill="none"/></svg>
  <svg class="abs arrow" style="left:1140px" width="14" height="24" viewBox="0 0 14 24"><path d="M2 2l10 10-10 10" stroke="#ddd" stroke-width="2.5" fill="none"/></svg>
  <div class="abs pshape" style="left:129px;border-radius:50%"></div>
  <div class="abs pshape" style="left:302px"></div>
  <div class="abs pshape" style="left:454px;background:none;border:2px solid #cfcfcf"></div>
  <div class="abs pshape" style="left:632px;border-radius:50%"></div>
  <div class="abs pshape" style="left:809px"></div>
  <div class="abs pshape" style="left:994px;border-radius:50%"></div>
</section>

<!-- footer -->
<footer class="section footer">
  <div class="abs fhead" style="left:112px">QUICK LINKS</div>
  <ul class="abs qlinks">
    <li>Home</li><li>About us</li><li>Services</li><li>Shipping</li><li>News</li><li>Gallery</li><li>Contact us</li>
  </ul>

  <div class="abs" role="img" aria-label="Silver scroll ornament with coloured gemstones" style="left:385px;top:30px;width:430px;height:170px;border-radius:20px;background:radial-gradient(ellipse at center,#5a5a5a,#1a1a1a 70%)"></div>

  <div class="abs field" style="left:350px;top:211px">👤︎ Name*</div>
  <div class="abs field" style="left:607px;top:211px">✉︎ Email Address*</div>
  <div class="abs field" style="left:350px;top:271px">✆︎ Phone*</div>
  <div class="abs field submit" style="left:607px;top:271px">➤ SUBMIT</div>

  <div class="abs fhead" style="left:874px">GET IN TOUCH</div>
  <div class="abs contact" style="top:110px">
    <svg width="9" height="12" viewBox="0 0 9 12"><path d="M4.5 0A4.5 4.5 0 0 0 0 4.5C0 8 4.5 12 4.5 12S9 8 9 4.5A4.5 4.5 0 0 0 4.5 0z" fill="#f4c400"/><circle cx="4.5" cy="4.5" r="1.6" fill="#0e0e0e"/></svg>
    <span>145, Lorem ipsum dolor sit am<br>et, consectetur adipiscing</span>
  </div>
  <div class="abs contact" style="top:213px">
    <svg width="11" height="11" viewBox="0 0 24 24"><path fill="#f4c400" d="M6.6 10.8a15 15 0 0 0 6.6 6.6l2.2-2.2c.3-.3.7-.4 1-.2 1.1.4 2.3.6 3.6.6.6 0 1 .4 1 1V20c0 .6-.4 1-1 1C10.6 21 3 13.4 3 4c0-.6.4-1 1-1h3.5c.6 0 1 .4 1 1 0 1.3.2 2.5.6 3.6.1.3 0 .7-.2 1z"/></svg>
    <span>+1 555 010 2030</span>
  </div>
  <div class="abs contact" style="top:283px">
    <svg width="12" height="9" viewBox="0 0 12 9"><rect width="12" height="9" fill="#f4c400"/><path d="M0 0l6 5 6-5" stroke="#0e0e0e" fill="none"/></svg>
    <span>info@kvrglobalinks.com</span>
  </div>

  <div class="abs fline"></div>
  <div class="abs center copy">Copyrights © 2020. All Rights Reserved | KVR Globalinks</div>
</footer>

</body>
</html>
```